Business Card for: Bramwell Financial Advisory Services Inc.

provide strategic financial advisory services to companies in the areas of corporate finance, mergers and acquisitions, executive coaching and strategic planning

Target Market(s)

Companies, banks, accountants, lawyers

Industry/Entity Type

High end business consulting in corporate finance, mergers and acquisitions, consulting

Contact Information for Business Card

Name of company, Name: xxxxxx xxxxxx , CEO, - phone number: 1-xxx-xxx-xxxx, - email address,

Requirements
Must have
• Must be professional and simple.
Nice to have
• simple, straight graphics, must give the impression that we are trustworthy, professional, competent
Should not have
• loud colors, loud design features

```html
<!DOCTYPE html>
<html lang="en">
<head>
<meta charset="utf-8">
<title>Bramwell Financial Advisory Services Inc. – Business Card</title>
<link rel="stylesheet" href="https://fonts.googleapis.com/css2?family=Tinos:wght@400;700&display=swap">
<style>
  :root {
    --navy: #002868;
    --orange: #ff6a0c;
    --ink: #111111;
    --paper: #ffffff;
    --backdrop: #9a9a9a;
  }
  * { box-sizing: border-box; margin: 0; padding: 0; }
  html, body { width: 1200px; height: 1059px; overflow: hidden; }
  body {
    background: var(--backdrop);
    position: relative;
    font-family: "Tinos", "Times New Roman", serif;
  }
  .card {
    position: absolute;
    left: 250px;
    width: 700px;
    height: 400px;
    border-radius: 28px;
    overflow: hidden;
  }
  .card--front { top: 85px; background: var(--paper); }
  .card--back { top: 570px; background: var(--navy); }

  .company {
    display: flex;
    align-items: center;
    font-family: "Tinos", "Times New Roman", serif;
    font-weight: 700;
    white-space: nowrap;
  }
  .company__square { flex: none; }
  .card--front .company {
    position: absolute;
    right: 40px;
    top: 68px;
    color: var(--navy);
    font-size: 21px;
  }
  .card--front .company__square {
    width: 14px; height: 14px;
    background: var(--orange);
    margin-right: 12px;
  }
  .card--back .company {
    position: absolute;
    left: 0; right: 0;
    top: 182px;
    justify-content: center;
    color: var(--paper);
    font-size: 28px;
  }
  .card--back .company__square {
    width: 18px; height: 18px;
    background: var(--orange);
    margin-right: 16px;
  }

  .holder { position: absolute; left: 40px; top: 193px; }
  .holder__name { color: var(--navy); font-weight: 700; font-size: 26px; }
  .holder__title { color: var(--ink); font-size: 17px; margin-top: 4px; }

  .divider {
    position: absolute;
    left: 40px; right: 40px; top: 268px;
    height: 1.5px;
    background: var(--ink);
  }

  .contacts { position: absolute; left: 40px; top: 284px; list-style: none; }
  .contacts__item {
    display: flex; align-items: center;
    height: 29.5px;
    font-size: 17px;
    color: var(--ink);
  }
  .contacts__icon { width: 20px; height: 20px; margin-right: 16px; flex: none; }

  .address {
    position: absolute;
    right: 40px; top: 308px;
    text-align: right;
    font-size: 17px;
    line-height: 25px;
    color: var(--ink);
    font-style: normal;
  }

  .accent-band { position: absolute; left: 0; bottom: 0; width: 700px; height: 13px; }
</style>
</head>
<body>
  <section class="card card--front" aria-label="Business card front">
    <div class="company"><span class="company__square"></span>Bramwell Financial Advisory Services Inc.</div>

    <div class="holder">
      <div class="holder__name">Daniel Whitford</div>
      <div class="holder__title">CEO</div>
    </div>

    <div class="divider"></div>

    <ul class="contacts">
      <li class="contacts__item">
        <svg class="contacts__icon" viewBox="0 0 24 24" aria-hidden="true">
          <path fill="var(--orange)" d="M6.6 10.8a15.1 15.1 0 0 0 6.6 6.6l2.2-2.2a1 1 0 0 1 1-.25 11.4 11.4 0 0 0 3.6.57 1 1 0 0 1 1 1V20a1 1 0 0 1-1 1A17 17 0 0 1 3 4a1 1 0 0 1 1-1h3.5a1 1 0 0 1 1 1c0 1.25.2 2.45.57 3.57a1 1 0 0 1-.25 1z"/>
        </svg>
        1-416-555-0182
      </li>
      <li class="contacts__item">
        <svg class="contacts__icon" viewBox="0 0 24 24" aria-hidden="true">
          <path fill="var(--orange)" d="M2 5h20v14H2z"/>
          <path fill="none" stroke="#fff" stroke-width="1.8" d="M2.5 5.5 12 13l9.5-7.5"/>
        </svg>
        info@bramwelladvisory.com
      </li>
      <li class="contacts__item">
        <svg class="contacts__icon" viewBox="0 0 24 24" aria-hidden="true">
          <circle cx="12" cy="12" r="10" fill="none" stroke="var(--orange)" stroke-width="2"/>
          <path fill="var(--orange)" d="M7 5.5c2 .5 3 2 2.5 3.5S6 10 6.5 12s3 2 3.5 4-1 3.5-1 4.5A9 9 0 0 1 4 8zM14 4c1 2 3 2 3.5 4s-2 2.5-1.5 4.5 3 1.5 4 1A8.5 8.5 0 0 0 14 4z"/>
        </svg>
        www.bramwelladvisory.com
      </li>
    </ul>

    <address class="address">
      421 Harbour Street, Suite 900<br>
      Toronto, ON M5J 2T3
    </address>

    <svg class="accent-band" viewBox="0 0 700 13" preserveAspectRatio="none" aria-hidden="true">
      <polygon points="0,0 341,0 348,13 0,13" fill="var(--orange)"/>
      <polygon points="348,0 700,0 700,13 356,13" fill="var(--navy)"/>
    </svg>
  </section>

  <section class="card card--back" aria-label="Business card back">
    <div class="company"><span class="company__square"></span>Bramwell Financial Advisory Services Inc.</div>
  </section>
</body>
</html>
```